Verodex business card

Business card for sustainable investment company called "Verodex". Verodex is an exchange platform selling carbon credits between buyers and sellers. Carbon Credits are an environmental commodity for reducing global carbon emissions.

the card should obviously have our logo and the theme should be sustainability/environment mixed with a trading platform.

Contact Information for Business Card

Logo, Name, Title, Phone, Email

Colors
0054AA
0677BA
7BADD7
CADEEF
E8F1F8
0094D4
00A9DD
6FCCEA
C7EBF8
E9F6FB
00AB8E
00BBA5
67D7C9
C6EFE9
E9F9F6
59FF00
82FF00
B8FF75
E3FFCB
F4FFEA

```html
<!DOCTYPE html>
<html lang="en">
<head>
<meta charset="UTF-8">
<title>Verodex business card</title>
<link href="https://fonts.googleapis.com/css2?family=Montserrat:wght@700;800&family=Lato:wght@300;400&display=swap" rel="stylesheet">
<style>
  :root {
    --stage: #e4e7eb;
    --card-navy: #14294f;
    --card-navy-deep: #10223f;
    --emboss: #1a3260;
    --accent-cyan: #4cc9e0;
    --accent-blue: #0094d4;
    --text-white: #ffffff;
  }
  * { margin: 0; padding: 0; box-sizing: border-box; }
  html, body {
    width: 1200px;
    height: 856px;
    overflow: hidden;
    background: var(--stage);
  }
  .stage {
    width: 1200px;
    height: 856px;
    display: flex;
    flex-direction: column;
    align-items: center;
    justify-content: center;
    gap: 30px;
  }
  .card {
    position: relative;
    width: 680px;
    height: 389px;
    background: var(--card-navy);
    box-shadow: 0 6px 18px rgba(16, 34, 63, 0.25);
    overflow: hidden;
  }

  /* front */
  .brand {
    position: absolute;
    left: 118px;
    top: 128px;
  }
  .brand-mark {
    width: 38px;
    height: 38px;
    background: var(--accent-blue);
    margin-bottom: 12px;
  }
  .brand-name {
    font-family: "Montserrat", sans-serif;
    font-weight: 800;
    font-size: 40px;
    letter-spacing: 0.5px;
    color: var(--text-white);
    line-height: 1;
  }
  .divider {
    position: absolute;
    left: 392px;
    top: 150px;
    width: 2px;
    height: 190px;
    background: var(--accent-cyan);
  }
  .person {
    position: absolute;
    left: 420px;
    top: 176px;
  }
  .person-name {
    font-family: "Montserrat", sans-serif;
    font-weight: 800;
    font-size: 23px;
    color: var(--accent-cyan);
    text-transform: uppercase;
    line-height: 1.1;
  }
  .person-title {
    font-family: "Lato", sans-serif;
    font-weight: 300;
    font-size: 17px;
    color: var(--text-white);
    margin-top: 4px;
  }
  .contacts {
    list-style: none;
    margin-top: 14px;
  }
  .contact {
    display: flex;
    align-items: center;
    gap: 8px;
    font-family: "Lato", sans-serif;
    font-weight: 400;
    font-size: 17px;
    color: var(--text-white);
    line-height: 1.45;
  }
  .contact svg {
    width: 12px;
    height: 12px;
    flex: none;
    fill: var(--accent-cyan);
  }

  /* back */
  .card-back .back-brand {
    position: absolute;
    left: 150px;
    top: 92px;
  }
  .back-mark {
    width: 90px;
    height: 90px;
    background: var(--emboss);
    margin-bottom: 20px;
  }
  .back-name {
    font-family: "Montserrat", sans-serif;
    font-weight: 800;
    font-size: 78px;
    color: var(--emboss);
    line-height: 1;
    letter-spacing: 1px;
  }
</style>
</head>
<body>
<main class="stage">

  <section class="card card-front" aria-label="Card front">
    <div class="brand">
      <div class="brand-mark"></div>
      <div class="brand-name">VERODEX</div>
    </div>

    <div class="divider"></div>

    <div class="person">
      <div class="person-name">Marcus Reed</div>
      <div class="person-title">Managing Director</div>
      <ul class="contacts">
        <li class="contact">
          <svg viewBox="0 0 24 24" aria-hidden="true"><path d="M6.6 10.8a15.1 15.1 0 0 0 6.6 6.6l2.2-2.2a1 1 0 0 1 1-.25 11.4 11.4 0 0 0 3.6.57 1 1 0 0 1 1 1V20a1 1 0 0 1-1 1A17 17 0 0 1 3 4a1 1 0 0 1 1-1h3.5a1 1 0 0 1 1 1c0 1.25.2 2.45.57 3.57a1 1 0 0 1-.25 1z"/></svg>
          123 456 789
        </li>
        <li class="contact">
          <svg viewBox="0 0 24 24" aria-hidden="true"><path d="M2 5h20v14H2zm2 2v.5l8 5 8-5V7l-8 5z"/></svg>
          info@verodexmail.com
        </li>
        <li class="contact">
          <svg viewBox="0 0 24 24" aria-hidden="true"><path d="M12 2a10 10 0 1 0 0 20 10 10 0 0 0 0-20zm0 2c.9 0 2.1 2 2.6 5H9.4C9.9 6 11.1 4 12 4zm-3 7h6c.1 1 .1 2 0 3H9c-.1-1-.1-2 0-3zm.4 5h5.2c-.5 3-1.7 4-2.6 4s-2.1-1-2.6-4z"/></svg>
          www.verodex-trade.com
        </li>
      </ul>
    </div>
  </section>

  <section class="card card-back" aria-label="Card back">
    <div class="back-brand">
      <div class="back-mark"></div>
      <div class="back-name">VERODEX</div>
    </div>
  </section>

</main>
</body>
</html>
```